BRISKEL Need a luxury modern business card designed.

Need a luxury modern business card designed. refer to the uploaded files for the company name and logo in the zip file under source files. i will making my descion on monday. so please send in before then so if we need to edit we will have the time. we have a trade show coming up and im on a deadline for printer.

Target Market(s)

high end clients

Contact Information for Business Card

Company nAme and logo. Tobias Fennick Co-Founder / Project Manager Office # 555-318-7094 Cell # 555-642-1586 BRISKEL.CA Tobias@briskel-example.ca

Font styles to use
Other font styles liked:
• Modern

Requirements
Must have
• Company name and logo, contact info, using the black, gold and white color scheme.

```html
<!DOCTYPE html>
<html lang="en">
<head>
<meta charset="utf-8">
<title>BRISKEL Business Card</title>
<link href="https://fonts.googleapis.com/css2?family=Montserrat:wght@300;400;500;600&display=swap" rel="stylesheet">
<style>
  :root {
    --stage: #1b1b1b;
    --charcoal: #323232;
    --paper: #ffffff;
    --gold: #a8955f;
    --ink: #2a2a2a;
    --soft-white: #f2f2f2;
  }
  * { box-sizing: border-box; margin: 0; padding: 0; }
  html, body {
    width: 1200px; height: 900px; overflow: hidden;
    background: var(--stage);
    font-family: "Montserrat", sans-serif;
  }
  .canvas { position: relative; width: 1200px; height: 900px; }
  .card {
    position: absolute; left: 280px; width: 640px; height: 366px;
    overflow: hidden;
    box-shadow: 0 18px 40px rgba(0,0,0,0.55);
  }
  .card-back { top: 62px; background: var(--charcoal); }
  .card-front { top: 472px; background: var(--paper); }

  .brand-name {
    font-weight: 300; letter-spacing: 0.22em; line-height: 1;
    white-space: nowrap;
  }
  .card-back .brand-name {
    position: absolute; left: 0; right: 0; top: 200px;
    text-align: center; font-size: 40px; color: var(--soft-white);
  }
  .card-front .brand-name {
    position: absolute; left: 40px; top: 128px;
    font-size: 42px; color: var(--ink);
  }

  .wave { position: absolute; left: 0; top: 0; width: 640px; height: 366px; }

  .person {
    position: absolute; right: 36px; top: 40px; text-align: right;
    white-space: nowrap;
  }
  .person-name {
    font-weight: 600; font-size: 24px; letter-spacing: 0.04em;
    color: var(--gold); text-transform: uppercase; line-height: 1.2;
  }
  .person-role {
    margin-top: 4px; font-size: 17px; color: var(--ink); line-height: 1.2;
  }

  .contact-list {
    position: absolute; right: 34px; bottom: 16px;
    list-style: none; text-align: right;
  }
  .contact-item {
    display: flex; align-items: center; justify-content: flex-end;
    gap: 12px; font-size: 17px; color: var(--soft-white);
    line-height: 26px; white-space: nowrap;
  }
  .contact-item .accent { color: var(--gold); }
  .contact-icon { width: 16px; height: 16px; flex: none; }
  .contact-icon * { fill: none; stroke: var(--gold); stroke-width: 1.4; stroke-linecap: round; stroke-linejoin: round; }
</style>
</head>
<body>
<main class="canvas">

  <section class="card card-back" aria-label="Card back">
    <div class="brand-name">BRISKEL</div>
  </section>

  <section class="card card-front" aria-label="Card front">
    <svg class="wave" viewBox="0 0 640 366" aria-hidden="true">
      <path d="M0 262 C 180 318 400 270 640 110 L640 126 C 400 292 180 336 0 282 Z" fill="var(--gold)"/>
      <path d="M0 312 C 200 352 420 300 640 146 L640 366 L0 366 Z" fill="var(--charcoal)"/>
    </svg>

    <div class="brand-name">BRISKEL</div>

    <div class="person">
      <div class="person-name">Tobias Fennick</div>
      <div class="person-role">Co-Founder | Project Manager</div>
    </div>

    <ul class="contact-list">
      <li class="contact-item">555-318-7094
        <svg class="contact-icon" viewBox="0 0 16 16"><path d="M4 2 L6.5 2 L7.5 5 L6 6.2 C6.8 8 8 9.2 9.8 10 L11 8.5 L14 9.5 L14 12 C14 13 13 14 12 14 C6.5 13.5 2.5 9.5 2 4 C2 3 3 2 4 2 Z"/></svg>
      </li>
      <li class="contact-item">555-642-1586
        <svg class="contact-icon" viewBox="0 0 16 16"><rect x="4.5" y="1.5" width="7" height="13" rx="1.2"/><path d="M7 12.2 L9 12.2"/></svg>
      </li>
      <li class="contact-item">Tobias@briskel-example.ca
        <svg class="contact-icon" viewBox="0 0 16 16"><rect x="1.5" y="3.5" width="13" height="9" rx="0.8"/><path d="M1.8 4 L8 9 L14.2 4"/></svg>
      </li>
      <li class="contact-item"><span>WWW.<span class="accent">BRISKEL</span>.CA</span>
        <svg class="contact-icon" viewBox="0 0 16 16"><circle cx="8" cy="8" r="6.3"/><ellipse cx="8" cy="8" rx="2.6" ry="6.3"/><path d="M1.7 8 L14.3 8 M2.8 4.8 L13.2 4.8 M2.8 11.2 L13.2 11.2"/></svg>
      </li>
    </ul>
  </section>

</main>
</body>
</html>
```